Business Card for Polygraph business in Africa

Business Card . Polygraph Examiner based in Tanzania, East Africa.
Business Card will be used to disseminate contact information to potential clients.
It should convey that I am a professional specifically in the polygraph field and perform my work with integrity.

I have attached the business card that I'm currently using, which I threw together myself initially. It's not professional enough.

Target Market(s)

Banks, Accounting Firms, Government Ministries, Gas, Oil, & Gemstone Mining Concerns, Wildlife Conservation NGOs, International companies located in East Africa.

Industry/Entity Type

Business

Contact Information for Business Card

Veritrace Kilonga
Miriam Holloway
PO Box 48317
Arusha, Tanzania
+255 612 839 274
miriamholloway@postvale.example

Colors
00a990
f37122
faa54b

Requirements
Must have
• - Veritrace Kilonga (with the word "Polygraph" being more prominent than the word "Tanzania")
• - Forensic Examinations
• - Employment Screening
• - Should contain a logo of the Continental Truthline Society (of which I'm a member)
• - I would like an accent design (such as the polygraph "squiggles" of a cardio tracing or such as that)
• - My contact information (less prominent, but large enough to read legibly). I would also consider putting the contact information on the second side of the card.
Nice to have
• My color suggestions are changeable.
Should not have
• Anything "cutesy" or "cartoonish"

```html
<!DOCTYPE html>
<html lang="en">
<head>
<meta charset="utf-8">
<title>Veritrace Kilonga – Business Card</title>
<link rel="stylesheet" href="https://fonts.googleapis.com/css2?family=Source+Sans+3:wght@400;600&family=Tinos&display=swap">
<style>
  :root {
    --stage: #000000;
    --card: #333438;
    --teal: #00a990;
    --orange: #f37122;
    --amber: #faa54b;
    --ink: #f2f2f2;
    --divider: #46474c;
    --seal: #ffffff;
    --seal-ring: #1c1f5e;
  }
  * { margin: 0; padding: 0; box-sizing: border-box; }
  html, body { width: 1200px; height: 900px; overflow: hidden; background: var(--stage); }
  .stage { position: relative; width: 1200px; height: 900px; }
  .card {
    position: absolute; top: 271px; width: 457px; height: 281px;
    background: var(--card); border-radius: 14px;
  }
  .card--front { left: 137px; }
  .card--back { left: 626px; }

  .brand { position: absolute; left: 0; top: 70px; width: 270px; text-align: center; }
  .brand__mark { display: block; margin: 0 auto; }
  .brand__name {
    margin-top: 10px;
    font-family: "Source Sans 3", sans-serif; font-weight: 600;
    font-size: 18px; color: var(--teal); letter-spacing: 0.5px;
  }
  .divider { position: absolute; left: 231px; top: 70px; width: 1px; height: 160px; background: var(--divider); }

  .contact { position: absolute; left: 247px; top: 66px; font-family: "Source Sans 3", sans-serif; color: var(--ink); }
  .contact__name { font-size: 18px; font-weight: 600; line-height: 1.2; }
  .contact__first { color: var(--teal); }
  .contact__last { color: var(--orange); }
  .contact__role { font-size: 13px; margin-top: 2px; }
  .contact__address { font-size: 13px; line-height: 19px; margin-top: 18px; }
  .contact__lines { list-style: none; margin-top: 11px; font-size: 13px; line-height: 20px; }
  .contact__lines li { display: flex; align-items: center; gap: 8px; }
  .contact__email { font-size: 12px; }
  .icon { width: 10px; height: 10px; flex: none; }

  .seal { position: absolute; left: 169px; top: 78px; }
  .services {
    position: absolute; left: 0; top: 216px; width: 457px; text-align: center;
    font-family: "Tinos", serif; font-size: 13px; line-height: 19px; color: var(--ink); letter-spacing: 0.3px;
  }
</style>
</head>
<body>
<main class="stage">
  <section class="card card--front">
    <div class="brand">
      <svg class="brand__mark" width="94" height="94" viewBox="0 0 94 94" aria-hidden="true">
        <circle cx="47" cy="47" r="47" fill="var(--teal)"/>
      </svg>
      <p class="brand__name">Veritrace Kilonga</p>
    </div>
    <span class="divider"></span>
    <div class="contact">
      <h1 class="contact__name"><span class="contact__first">Miriam</span> <span class="contact__last">Holloway</span></h1>
      <p class="contact__role">Polygraph Examiner</p>
      <p class="contact__address">PO Box 48317<br>Arusha, Tanzania</p>
      <ul class="contact__lines">
        <li>
          <svg class="icon" viewBox="0 0 10 10" aria-hidden="true"><path d="M2 1 L3.6 1 L4.2 3 L3.1 3.8 Q4.2 6 6.2 6.9 L7 5.8 L9 6.4 L9 8 Q8.5 9 7.5 9 Q1 8 1 2.5 Q1 1.4 2 1 Z" fill="var(--teal)"/></svg>
          <span>+255 612 839 274</span>
        </li>
        <li>
          <svg class="icon" viewBox="0 0 10 10" aria-hidden="true"><rect x="0.5" y="2" width="9" height="6.5" fill="var(--teal)"/><path d="M0.8 2.3 L5 5.5 L9.2 2.3" stroke="var(--card)" stroke-width="0.9" fill="none"/></svg>
          <span class="contact__email">miriamholloway@postvale.example</span>
        </li>
      </ul>
    </div>
  </section>

  <section class="card card--back">
    <svg class="seal" width="120" height="120" viewBox="0 0 120 120" role="img" aria-label="Membership seal of the Continental Truthline Society">
      <circle cx="60" cy="60" r="59" fill="var(--seal)"/>
      <circle cx="60" cy="60" r="54" fill="none" stroke="var(--seal-ring)" stroke-width="3"/>
    </svg>
    <p class="services">FORENSIC EXAMINATIONS<br>EMPLOYMENT SCREENING</p>
  </section>
</main>
</body>
</html>
```